Pool Screen Enclosure Building a Career Boot Camp!

Looking to Host a Boot Camp for people looking for a career or looking to change careers. We Design, Manufacture and Install Custom Pool Screen Enclosures. We have a training program to allow Non Experienced motivated people the chance at a great career that will provide a great living for them and their family. This will be a paid boot camp, week long, we provide all the initial training for them to make a transition into our business. This will be 5 days of training with a guaranteed job to start the following Monday.... This is good for both someone with no construction experience or someone with construction experience that wants to upgrade their current job.
Paid Boot Camp
transition to a full time job with great pay
Benefits include Health Insurance, Dental and Vision, 401K, we provide the tools and training.

```html
<!DOCTYPE html>
<html lang="en">
<head>
<meta charset="utf-8">
<title>Pool Screen Enclosure Bootcamp – Lanai Works</title>
<link rel="stylesheet" href="https://fonts.googleapis.com/css2?family=Anton&family=Montserrat:wght@500;600&family=Arimo:wght@700&display=swap">
<style>
  :root {
    --green: #4daf17;
    --white: #ffffff;
    --ink: #0d0d0d;
    --sky-top: #7f9cbc;
    --sky-low: #c9d3dc;
    --field: #5f7a3c;
  }
  * { margin: 0; padding: 0; box-sizing: border-box; }
  html, body { width: 945px; height: 1200px; overflow: hidden; background: var(--white); }
  .flyer { position: relative; width: 945px; height: 1200px; overflow: hidden; background: var(--white); }
  .abs { position: absolute; }

  .hero-photo {
    left: 0; top: 0; width: 945px; height: 538px;
    background: linear-gradient(180deg, var(--sky-top) 0%, var(--sky-low) 55%, #a9b29a 80%, var(--field) 100%);
  }
  .headline { left: 0; top: 0; width: 945px; height: 538px; }
  .headline text, .band-title text, .career-line text, .guarantee text {
    font-family: "Anton", "Impact", sans-serif;
  }

  .band-title { left: 0; top: 538px; width: 945px; height: 70px; }
  .questions {
    left: 15px; top: 609px; width: 915px;
    font-family: "Montserrat", sans-serif; font-weight: 500;
    font-size: 18.6px; color: var(--ink); white-space: nowrap; letter-spacing: -0.1px;
  }

  .benefit-band { left: 0; top: 646px; width: 945px; height: 138px; background: var(--green); }
  .benefit-list {
    left: 21px; top: 659px;
    font-family: "Montserrat", sans-serif; font-weight: 600;
    font-size: 22px; line-height: 27.5px; color: var(--ink); list-style: none;
  }
  .career-pitch {
    left: 325px; top: 659px; width: 606px; text-align: center;
    font-family: "Montserrat", sans-serif; font-weight: 600;
    font-size: 20.5px; line-height: 26px; color: var(--white);
  }
  .contact {
    left: 325px; top: 747px; width: 606px; text-align: center;
    font-family: "Montserrat", sans-serif; font-weight: 600;
    font-size: 21px; color: var(--ink);
  }

  .guarantee { left: 0; top: 795px; width: 945px; height: 48px; }

  .photo-strip { left: 0; top: 850px; width: 945px; height: 298px; }
  .photo-training { left: 0; top: 0; width: 314px; height: 298px;
    background: linear-gradient(160deg, #b3aea2 0%, #8e8172 60%, #6c5f50 100%); }
  .photo-enclosure { left: 315px; top: 0; width: 321px; height: 298px;
    background: linear-gradient(180deg, #d4d6da 0%, #9ea3a8 55%, #4f8c9c 85%, #6d7d70 100%); }
  .photo-install { left: 637px; top: 0; width: 308px; height: 298px;
    background: linear-gradient(180deg, #5d82b8 0%, #9fb4cf 55%, #d9dde2 100%); }
  .career-line { left: 0; top: 1038px; width: 945px; height: 76px; }

  .footer { left: 0; top: 1148px; width: 945px; height: 52px; background: var(--green); }
  .address {
    left: 30px; top: 1172px;
    font-family: "Arimo", "Arial", sans-serif; font-weight: 700;
    font-size: 14.6px; color: var(--ink); white-space: nowrap;
  }
  .phone {
    left: 630px; top: 1158px;
    font-family: "Arimo", "Arial", sans-serif; font-weight: 700;
    font-size: 37px; line-height: 1; color: var(--ink); white-space: nowrap; letter-spacing: 0.5px;
  }
</style>
</head>
<body>
<main class="flyer">
  <div class="abs hero-photo" role="img" aria-label="Worker on a ladder stretching screen across a pool enclosure frame under a cloudy sky"></div>
  <svg class="abs headline" viewBox="0 0 945 538" aria-label="Pool Screen Enclosure Bootcamp">
    <text x="30" y="107" font-size="96" fill="#fff" textLength="883" lengthAdjust="spacingAndGlyphs">POOL SCREEN ENCLOSURE</text>
    <text x="30" y="495" font-size="206" fill="#fff" textLength="883" lengthAdjust="spacingAndGlyphs">BOOTCAMP</text>
  </svg>

  <svg class="abs band-title" viewBox="0 0 945 70">
    <text x="15" y="62" font-size="50" fill="#0d0d0d" textLength="915" lengthAdjust="spacingAndGlyphs">TRANSITION TO A FULL TIME JOB WITH GREAT PAY</text>
  </svg>
  <p class="abs questions">ARE YOU MOTIVATED? HARDWORKING?&nbsp; ARE YOU LOOKING FOR A NEW OPPORTUNITY?</p>

  <section class="abs benefit-band"></section>
  <ul class="abs benefit-list">
    <li>BENEFITS INCLUDE:</li>
    <li>-HEALTH INSURANCE</li>
    <li>-DENTAL AND VISION</li>
    <li>-401K</li>
  </ul>
  <p class="abs career-pitch">A REWARDING CAREER THAT CAN PROVIDE A GREAT<br>LIVING FOR YOU AND YOUR FAMILY.<br>NO CONSTRUCTION EXPERIENCE REQUIRED!</p>
  <p class="abs contact">To Join contact: admin@lanaiworksco.com</p>

  <svg class="abs guarantee" viewBox="0 0 945 48">
    <text x="15" y="39" font-size="33" fill="#0d0d0d" textLength="915" lengthAdjust="spacingAndGlyphs">5 DAYS OF TRAINING WITH A GUARANTEED JOB - TOOLS AND TRAINING PROVIDED</text>
  </svg>

  <div class="abs photo-strip">
    <div class="abs photo-training" role="img" aria-label="Trainees crouched around a set of plans on a job site"></div>
    <div class="abs photo-enclosure" role="img" aria-label="Finished screened pool enclosure at dusk"></div>
    <div class="abs photo-install" role="img" aria-label="Two installers fitting a white enclosure beam against a blue sky"></div>
  </div>
  <svg class="abs career-line" viewBox="0 0 945 76">
    <text x="33" y="69" font-size="80" fill="#fff" textLength="880" lengthAdjust="spacingAndGlyphs">YOUR NEW SHOT AT A CAREER</text>
  </svg>

  <footer class="abs footer"></footer>
  <p class="abs address">LANAI WORKS 218 N 12TH STREET, HARBOR BEND, FL - 34000</p>
  <p class="abs phone">555- 019 2846</p>
</main>
</body>
</html>
```